Creative, fresh business card design for Ripplecraft Facades

We need a fresh, creative business card design for Ripplecraft Facades. We are the manufacturer of Ripplecraft Facades in Australia. Wall panels are 2400 x 1200mm panels made from MDF and feature 3D patterns on the face of the panel. The colours to be used are green, silver/grey and white RGB
Red 187
Green 207
Blue 65.

An idea is to possibly use a watermark of one of our designs as a background (like on the "Grids" design on the left hand side of page 2 of our brochure).

Target Market(s)

Interior designers, architects, builders and home renovators

Industry/Entity Type

Business

Contact Information for Business Card

Details to go on the card are:
Our logo (attached),
Slogan: "Decorative panels for interiors and exteriors",
Contact name,
Position,
Mobile phone number,
Business address,
Business phone,
Business fax,
Website and
Email address.

I have attached a few images of our panels and our brochure for reference.

The colours of the business card should feature our logo colours which are: RGB
Red 187
Green 207
Blue 65

Requirements
Must have
• Very modern fonts and design. Some of the designs shown especially the "Prisms" design which is a popular design.
Nice to have
• Creative but simple design. Very contemporary.
Should not have
• Anything ornate or old fashioned.

```html
<!DOCTYPE html>
<html lang="en">
<head>
<meta charset="utf-8">
<title>Ripplecraft Facades – Business Card</title>
<link rel="stylesheet" href="https://fonts.googleapis.com/css2?family=Raleway:wght@300;400&display=swap">
<style>
  :root {
    --page: #e4e1dc;
    --card: #111111;
    --card-edge: #1c1c1c;
    --lime: rgb(187, 207, 65);
    --silver: #b9b9b9;
    --text: #d6d6d6;
    --muted: #9a9a9a;
  }
  * { box-sizing: border-box; margin: 0; padding: 0; }
  html, body { width: 1200px; height: 1022px; overflow: hidden; }
  body {
    background: var(--page);
    font-family: "Raleway", Arial, sans-serif;
    font-weight: 300;
    color: var(--text);
    position: relative;
  }
  .card {
    position: absolute;
    left: 280px;
    width: 640px;
    height: 366px;
    background: var(--card);
    border-radius: 4px;
    overflow: hidden;
    box-shadow: 0 14px 30px rgba(0,0,0,.35);
  }
  .card--front { top: 100px; }
  .card--back { top: 556px; }
  .ripple-texture {
    position: absolute; inset: 0;
    background: radial-gradient(circle at 70% 30%, #202020 0%, var(--card-edge) 35%, var(--card) 80%);
  }
  .edge-strip {
    position: absolute; left: 0; top: 0; bottom: 0; width: 10px;
    background: var(--lime);
  }
  .edge-strip::after {
    content: ""; position: absolute; left: 10px; top: 0; bottom: 0; width: 5px;
    background: var(--silver);
  }
  .brand {
    position: absolute;
    display: flex; align-items: center; gap: 12px;
  }
  .brand__square { background: var(--lime); flex: none; }
  .brand__name { color: #ffffff; font-weight: 300; white-space: nowrap; }
  .slogan {
    position: absolute; color: var(--muted);
    letter-spacing: 2px; text-transform: lowercase; line-height: 1.35;
  }
  .card--front .brand { top: 46px; right: 44px; }
  .card--front .brand__square { width: 44px; height: 44px; }
  .card--front .brand__name { font-size: 22px; }
  .card--front .slogan { top: 100px; right: 44px; font-size: 12px; text-align: right; }
  .person { position: absolute; left: 48px; top: 150px; }
  .person__name { color: var(--lime); font-size: 26px; font-weight: 400; }
  .person__role { font-size: 15px; color: var(--text); margin-top: 2px; letter-spacing: 1px; }
  .contacts { position: absolute; left: 48px; top: 222px; list-style: none; font-size: 14.5px; letter-spacing: .8px; }
  .contacts li { display: flex; align-items: center; gap: 12px; height: 22px; }
  .contacts svg { width: 14px; height: 14px; fill: none; stroke: var(--lime); stroke-width: 1.6; flex: none; }
  .address { position: absolute; left: 330px; top: 266px; font-size: 14.5px; line-height: 22px; letter-spacing: .8px; }
  .card--back .brand { top: 140px; left: 50%; transform: translateX(-50%); gap: 18px; }
  .card--back .brand__square { width: 62px; height: 62px; }
  .card--back .brand__name { font-size: 34px; }
  .card--back .slogan { top: 224px; left: 0; right: 0; text-align: center; font-size: 13px; }
  .card--back .top-band {
    position: absolute; top: 0; left: 0; right: 0; height: 8px; background: var(--silver);
  }
</style>
</head>
<body>

<section class="card card--front">
  <div class="ripple-texture" role="img" aria-label="Faint embossed ripple panel pattern across the card"></div>
  <div class="edge-strip"></div>

  <div class="brand">
    <span class="brand__square"></span>
    <span class="brand__name">Ripplecraft Facades</span>
  </div>
  <p class="slogan">decorative panels for<br>interiors &amp; landscapes</p>

  <div class="person">
    <p class="person__name">Owen Halloway</p>
    <p class="person__role">President</p>
  </div>

  <ul class="contacts">
    <li><svg viewBox="0 0 14 14"><rect x="3.5" y="1" width="7" height="12" rx="1.2"/><line x1="6" y1="11" x2="8" y2="11"/></svg>212. 555. 0148</li>
    <li><svg viewBox="0 0 14 14"><path d="M3 1.5l2.2 2.6-1.3 1.6c.9 1.8 2.4 3.3 4.3 4.3l1.6-1.3 2.6 2.2-1.4 1.6C6.4 12.4 1.6 7.6 1.5 3z"/></svg>212. 555. 0162</li>
    <li><svg viewBox="0 0 14 14"><rect x="1.5" y="5" width="11" height="6" rx="1"/><rect x="4" y="1.5" width="6" height="3.5"/><rect x="4" y="9" width="6" height="3.5"/></svg>212. 555. 0175</li>
    <li><svg viewBox="0 0 14 14"><rect x="1.5" y="3" width="11" height="8"/><path d="M1.5 3l5.5 4.5L12.5 3"/></svg>owen@ripplecraft.co</li>
    <li><svg viewBox="0 0 14 14"><circle cx="7" cy="7" r="5.5"/><ellipse cx="7" cy="7" rx="2.3" ry="5.5"/><line x1="1.5" y1="7" x2="12.5" y2="7"/></svg>www.ripplecraft.co</li>
  </ul>

  <p class="address">2140 Harbour Road<br>Bayview, NSW 2104</p>
</section>

<section class="card card--back">
  <div class="ripple-texture" role="img" aria-label="Faint embossed ripple panel pattern across the card"></div>
  <div class="top-band"></div>
  <div class="brand">
    <span class="brand__square"></span>
    <span class="brand__name">Ripplecraft Facades</span>
  </div>
  <p class="slogan">decorative panels for interiors &amp; landscapes</p>
</section>

</body>
</html>
```